Uncoded front page web design for wedding and event planning company

Hi.

I am launching a wedding and event planning company called Silver Fern Celebrations and need a professional and appealing web design.

So, let me explain my company. I am based in Swindon in Wiltshire but the company will plan weddings and events in Oxfordshire, Wiltshire, Berkshire and London.

We will plan weddings, birthdays, conferences, product launches, fashion shows and conventions but the main focus of the website at this stage should be the weddings with all the other occasions being covered under a single 'events' heading.

My contact details for the website should be:
Maureen Hollis
maureen@silverferncelebrations.co.uk
01793 587203 / 07781 452638

I'd like the website to feel clean, bright and elegant and be set against a white or off-white background. My logo is purple and I'd therefore like some purple incorporated into the design although feel free to use a more muted purple as my one might be a little bright? I'm also considering whether it would look nice paired with a little of the colour gold - maybe as a font colour in places?? I'll leave you to figure that one out as your design eye will be better than mine but for your reference below is my purple colour and my suggested gold one....

My purple colour is Pantone 2592 C but feel free to use others
My suggested gold I'm looking at is Pantone 14-1041 TCX

I would like to incorporate a Facebook feed in the front page if possible, if it looks right. I'd also like to include a variety of pictures as well so I've included a few in a Dropbox folder which is linked below. Please don't feel obliged to use them all by any means (there's loads!) but you've got a few there to play with. If you find any other royalty free images you'd rather use please go ahead but on the understanding I can have them afterwards!

My logo can be retrieved via this Dropbox link...
You'll notice there are 2 styles of placement. Please feel free to use either to fit in with your design...
https://www.filevault.example/sh/kq8pw2mzr4tn7ab/BBBQrt6hNxyvpe5L81GmsWd3Pc?dl=0

The wedding images I have are in this Dropbox folder...
https://www.filevault.example/sh/m9vc2xh6pl1qw8j/BBB4zkrNvLpte6P57YhaJoscb?dl=0

Other than that, it's over to you.... I can't wait to receive your designs :-)

Ooh....finally just to say, as I receive designs in I think I'll notice aspects that I like and don't like and if I feel they'll be useful for other designers, I'll update my brief below. Thanks

BRIEF UPDATE:
Someone asked if I had a tag-line. Could you use "Creating exquisite occasions today for amazing memories tomorrow"

I realise I hadn't explained what I'd like included on my home page so here's some notes to consider....

A welcome to section for me to start narrative about us and our services which has a button that links to our 'about us' page and 'services' page for further information.

A section that nicely illustrates what services we offer whether that be with icons or pictures.

A section with some photos in that would link to our gallery

A section that shows some customer reviews and blog entries that would link to my reviews page and blog to read more.

And finally a contact us section with my details, social media links and site map.

***
I also need to draw attention to where in the UK my services cover. I was therefore thinking perhaps we could use a picture to demonstrate this where it highlights Wiltshire, Oxfordshire, Berkshire and London on a map thereby demonstrating our areas covered. I have found several English county maps when searching on Google but I'm not sure how to highlight the areas I cover (or dull out the areas I don't) so if you have any ideas on this, I'd really like it incorporated. Thanks. (by the way, for those of you not familiar with English counties, the ones I cover are often abbreviated to Wilts, Oxon, Berks, London, so if you find a suitable map with those names on rather than the full names, you'll know what they are!)

I've found an image of the county map which might work well. I was wondering whether we might somehow grey out the counties I don't cover and just keep the ones I do as mentioned above and then crop it into perhaps a shadowed circle? I've attached a screenshot to the brief.

I've decided on the tag-line "Creating exquisite occasions today for amazing memories tomorrow" so if that could be included somewhere that would be great. I also need to draw attention to where in the UK my services cover. I was therefore thinking perhaps we could use a picture to demonstrate this where it highlights Wiltshire, Oxfordshire, Berkshire and London on a map thereby demonstrating our areas covered. I have found several English county maps when searching on Google but I'm not sure how to highlight the areas I cover (or dull out the areas I don't) so if you have any ideas on this, I'd really like it incorporated. Thanks. Added Wednesday, June 24, 2015

Target Market(s)

Predominately women aged 25-55

Industry/Entity Type

Wedding Planner

Number of Pages Required

1 page

Font styles to use
Sans Serif
Script

Requirements
Nice to have
• I'd like to see how the colour theme of purple and perhaps a little gold (maybe as a font colour) look against a white background. I've mentioned the Pantone colours in the brief above.
• I've attached a screenshot of a webpage with gold writing in and fonts that I like. Perhaps it could give you inspiration?
Should not have
• I really don't like the font SCRIPTINA so please done use that.

```html
<!DOCTYPE html>
<html lang="en">
<head>
<meta charset="utf-8">
<title>Silver Fern Celebrations</title>
<link rel="stylesheet" href="https://fonts.googleapis.com/css2?family=Raleway:wght@400;500;700&family=Roboto+Condensed:wght@400&display=swap">
<style>
:root{
  --cream:#f6efde;
  --cream-light:#f8f2e6;
  --mint:#a4d0bb;
  --mint-line:#e4f1ea;
  --gold:#a88c5d;
  --gold-frame:#e8cf9c;
  --purple:#8b2a9c;
  --ink:#2b2118;
  --text:#3a3a3a;
}
*{margin:0;padding:0;box-sizing:border-box}
html,body{width:698px;height:1200px;overflow:hidden}
body{background:var(--cream);font-family:"Raleway",sans-serif;color:var(--text);position:relative}
.abs{position:absolute}
.brand{left:0;width:698px;top:18px;display:flex;justify-content:center;align-items:center;gap:10px}
.brand-mark{width:40px;height:40px;border-radius:50%;border:2px solid var(--purple)}
.brand-name{color:var(--purple);font-weight:500;font-size:24px;line-height:1;white-space:nowrap}
.nav-rule{left:45px;width:608px;height:1px;background:var(--mint)}
.nav{top:96px;left:0;width:698px;font-family:"Roboto Condensed",sans-serif;font-size:11px;color:#555;letter-spacing:.2px}
.nav span{position:absolute;top:0;white-space:nowrap}
.nav .current{color:var(--gold)}
.photo{display:block}
.hero{left:45px;top:136px;width:408px;height:194px;background:radial-gradient(circle at 62% 45%,#e0a046 0,#c85a78 25%,#8e62b8 45%,#d8d4d6 70%,#c9c6c4 100%)}
.dot{top:307px;width:11px;height:11px;background:#000}
.dot.active{background:var(--gold)}
.dream{left:471px;top:136px;width:182px;height:90px;background:var(--mint)}
.inner-frame{position:absolute;inset:6px;border:1px solid var(--mint-line)}
.dream-title{left:0;top:24px;width:182px;text-align:center;font-size:13.5px;color:var(--ink);white-space:nowrap}
.dream-btn{left:14px;top:50px;width:154px;height:26px;background:var(--cream-light);color:var(--ink);font-size:12.5px;text-align:center;line-height:26px;white-space:nowrap}
.party{left:471px;top:239px;width:182px;height:91px;background:linear-gradient(135deg,#6d6a6a,#a8a2a0 50%,#5f5a5c)}
.party-frame{position:absolute;left:6px;top:6px;right:6px;bottom:6px;border:1px solid #111}
.tagline{left:45px;top:348px;width:608px;height:102px;background:var(--mint);text-align:center;color:var(--ink)}
.tag-1{position:absolute;left:0;width:100%;top:12px;font-size:27px;white-space:nowrap}
.tag-2{position:absolute;left:0;width:100%;top:50px;font-size:27px;white-space:nowrap}
.tag-2 strong{font-size:32px;font-weight:700}
.section-title{left:0;width:698px;text-align:center;color:var(--gold);font-size:25px;top:474px;white-space:nowrap}
.rule{height:2.4px;background:var(--gold)}
.intro{left:104px;width:490px;top:532px;text-align:center;font-size:8.8px;line-height:13.6px;color:#222}
.card-img{top:598px;width:181px;height:111px;border:2.5px solid var(--gold-frame)}
.img-church{background:linear-gradient(180deg,#7a6048,#a58a6c 45%,#5c3a2a)}
.img-table{background:linear-gradient(180deg,#1d2340,#6b5fa8 40%,#d9d6de)}
.img-list{background:linear-gradient(135deg,#f4f2ee,#e6e4e0)}
.card-title{top:721px;width:181px;text-align:center;color:var(--gold);font-size:15px;white-space:nowrap}
.card-text{top:759px;width:181px;text-align:center;font-size:8.6px;line-height:13.6px}
.more{top:810px;width:85px;height:26px;background:var(--mint);font-size:10px;color:var(--ink);text-align:center;line-height:26px;white-space:nowrap}
.more .inner-frame{inset:3px}
.reviews{left:45px;top:859px;width:608px;height:243px;background:var(--mint);text-align:center}
.reviews-title{position:absolute;left:0;width:100%;top:26px;font-size:23px;color:var(--ink);white-space:nowrap}
.quote{top:80px}
.review-text{position:absolute;left:59px;width:490px;top:79px;font-size:8.8px;line-height:13.6px;color:#333}
.avatar{left:275px;top:128px;width:72px;height:72px;border-radius:50%;border:2px solid #fff;background:radial-gradient(circle,#e4d8cc,#b9a594)}
.client{position:absolute;left:0;width:100%;top:208px;font-size:9.5px;font-weight:700;color:var(--ink)}
.social{top:1129px;width:30px;height:30px;border-radius:50%;border:1.5px solid #333}
.copy{left:0;width:698px;top:1175px;text-align:center;font-size:8px;color:#333}
.copy strong{font-weight:700}
</style>
</head>
<body>

<header>
  <div class="abs brand">
    <span class="brand-mark"></span>
    <span class="brand-name">Silver Fern Celebrations</span>
  </div>
  <div class="abs nav-rule" style="top:86px"></div>
  <nav class="abs nav">
    <span class="current" style="left:162px">HOME</span>
    <span style="left:219px">ABOUT</span>
    <span style="left:283px">SERVICES</span>
    <span style="left:360px">COURSE</span>
    <span style="left:430px">SHOP</span>
    <span style="left:484px">CONTACT</span>
  </nav>
  <div class="abs nav-rule" style="top:117px"></div>
</header>

<section>
  <div class="abs hero photo" role="img" aria-label="Bridal bouquet of colourful roses"></div>
  <span class="abs dot active" style="left:191px"></span>
  <span class="abs dot" style="left:216px"></span>
  <span class="abs dot" style="left:240px"></span>
  <span class="abs dot" style="left:264px"></span>

  <div class="abs dream">
    <div class="inner-frame"></div>
    <div class="abs dream-title">MAKE YOUR DREAM</div>
    <div class="abs dream-btn">Contact Maureen Hollis</div>
  </div>

  <div class="abs party photo" role="img" aria-label="Bride and guests celebrating under confetti">
    <div class="party-frame"></div>
  </div>
</section>

<section class="abs tagline">
  <div class="inner-frame"></div>
  <div class="tag-1">Creating Exquisite Occasions Today For</div>
  <div class="tag-2"><strong>Amazing Memories</strong> Tomorrow</div>
</section>

<section>
  <h1 class="abs section-title" style="font-weight:400">Welcome to Silver Fern</h1>
  <div class="abs rule" style="left:309px;top:512px;width:81px"></div>
  <p class="abs intro">Lorem Ipsum is simply dummy text of the printing and typesetting industry. Lorem Ipsum has been the industry's standard dummy text ever since the 1500s, when an unknown printer took a galley of type and scrambled it to make a type specimen book.</p>
</section>

<section>
  <div class="abs card-img img-church" style="left:45px" role="img" aria-label="Church aisle decorated for a wedding"></div>
  <div class="abs card-title" style="left:45px">Full Planning</div>
  <div class="abs rule" style="left:112px;top:744px;width:48px"></div>
  <p class="abs card-text" style="left:45px">Lorem Ipsum is simply dummy text of the printing and typesetting industry. Lorem Ipsum has been the industry.</p>
  <div class="abs more" style="left:91px"><div class="inner-frame"></div>READ MORE</div>

  <div class="abs card-img img-table" style="left:258px" role="img" aria-label="Reception table with floral centrepiece"></div>
  <div class="abs card-title" style="left:258px">Styling</div>
  <div class="abs rule" style="left:324px;top:744px;width:48px"></div>
  <p class="abs card-text" style="left:258px">Lorem Ipsum is simply dummy text of the printing and typesetting industry. Lorem Ipsum has been the industry.</p>
  <div class="abs more" style="left:304px"><div class="inner-frame"></div>READ MORE</div>

  <div class="abs card-img img-list" style="left:470px" role="img" aria-label="Handwritten wedding checklist with a red pencil"></div>
  <div class="abs card-title" style="left:470px">Budget</div>
  <div class="abs rule" style="left:537px;top:744px;width:48px"></div>
  <p class="abs card-text" style="left:470px">Lorem Ipsum is simply dummy text of the printing and typesetting industry. Lorem Ipsum has been the industry.</p>
  <div class="abs more" style="left:517px"><div class="inner-frame"></div>READ MORE</div>
</section>

<section class="abs reviews">
  <div class="inner-frame"></div>
  <h2 class="reviews-title" style="font-weight:400">Our Client Say</h2>
  <div class="abs rule" style="left:263px;top:62px;width:82px;background:var(--ink)"></div>
  <svg class="abs quote" style="left:25px" width="25" height="19" viewBox="0 0 25 19" aria-hidden="true">
    <path d="M0 19V10Q0 2 9 0l1 3Q5 5 5 9h5v10zM14 19V10q0-8 9-10l1 3q-5 2-5 6h5v10z" fill="#6cab8d"/>
  </svg>
  <svg class="abs quote" style="left:558px" width="25" height="19" viewBox="0 0 25 19" aria-hidden="true">
    <path d="M25 0v9q0 8-9 10l-1-3q5-2 5-6h-5V0zM11 0v9q0 8-9 10l-1-3q5-2 5-6H1V0z" fill="#6cab8d"/>
  </svg>
  <p class="review-text">Lorem Ipsum is simply dummy text of the printing and typesetting industry. Lorem Ipsum has been the industry's standard dummy text ever since the 1500s, when an unknown printer took a galley of type and scrambled it to make a type specimen book.</p>
  <div class="abs avatar" role="img" aria-label="Portrait photo of the client"></div>
  <div class="client">- Client Name</div>
</section>

<footer>
  <span class="abs social" style="left:285px" aria-label="Social link"></span>
  <span class="abs social" style="left:334px" aria-label="Social link"></span>
  <span class="abs social" style="left:383px" aria-label="Social link"></span>
  <p class="abs copy">© <strong>SILVER FERN</strong> - 2015. All Rights Reserved.</p>
</footer>

</body>
</html>
```